Detail Shop Business card design

i need a business card design for my new detailing company called 'Brisk's Polish Works'. i want an all black and white design . simple, direct and to the point. i want the designer to choose a fitting font to match the logothe front should have logo, address, phone and email and the back side should have a slogan and text indicating that we offer services on anything including cars, trucks, motorcycles and RVs. slogan will read "we take pride in your ride"
maybe also very small on the back side the IG icon with Brisks_Polish_Works

phone 208.417.6352
address 3847 E Larkin Ave
Spokane WA 99214
email: BrisksPolish@mailvexo.com

Target Market(s)

all ages , auto enthusiasts

Industry/Entity Type

Automotive

Contact Information for Business Card

the front should have logo, address, phone and email and the back side should have a slogan and text indicating that we offer services on anything including cars, trucks, motorcycles and RVs. slogan will read "we take pride in your ride"

phone 208.417.6352
address 3847 E Larkin Ave
Spokane WA 99214

Colors
000000
ffffff

Requirements
Must have
• bold font and very simple design with good spacing
Nice to have
• anything creative from the designer indicating we service any types of vehicles
Should not have
• any colors ,

```html
<!DOCTYPE html>
<html lang="en">
<head>
<meta charset="utf-8">
<title>Brisk's Polish Works – Business Card</title>
<link rel="stylesheet" href="https://fonts.googleapis.com/css2?family=Lato:wght@400;700;900&display=swap">
<style>
  :root {
    --backdrop: #9a9a9a;
    --ink: #000000;
    --paper: #ffffff;
    --soft-white: #f0f0f0;
    --rule-light: #9c9c9c;
    --rule-dark: #6e6e6e;
  }
  * { margin: 0; padding: 0; box-sizing: border-box; }
  html, body {
    width: 1200px; height: 900px; overflow: hidden;
    background: var(--backdrop);
    font-family: "Lato", Arial, sans-serif;
  }
  .stage { position: relative; width: 1200px; height: 900px; }

  .card { position: absolute; width: 478px; height: 293px; }
  .card--front {
    left: 120px; top: 275px;
    background: var(--paper); color: var(--ink);
    border-radius: 0 46px 0 46px;
  }
  .card--back {
    left: 606px; top: 274px;
    background: var(--ink); color: var(--soft-white);
    border-radius: 46px 0 46px 0;
  }

  /* Brand name block */
  .brand {
    position: absolute; left: 262px; top: 58px; width: 180px;
    display: flex; align-items: center; gap: 10px;
  }
  .brand__dot {
    flex: none; width: 16px; height: 16px; border-radius: 50%;
    background: var(--ink);
  }
  .brand__name {
    font-weight: 900; font-size: 25px; line-height: 1.1;
    text-transform: uppercase; color: var(--ink);
  }

  /* Social row */
  .social {
    position: absolute; left: 32px; top: 193px; width: 412px;
    display: flex; align-items: center; gap: 6px;
    font-size: 13.5px;
  }
  .social__dot {
    flex: none; width: 19px; height: 19px; border-radius: 50%;
    background: var(--ink);
  }
  .social__rule { flex: 1; height: 1px; background: var(--rule-light); margin-top: 6px; }

  .contact {
    position: absolute; left: 32px; top: 232px;
    font-size: 14px; line-height: 17px;
  }
  .contact__row { display: flex; align-items: center; gap: 4px; }
  .contact__row svg { flex: none; }

  .address {
    position: absolute; right: 34px; top: 234px;
    font-size: 14px; line-height: 17px; text-align: right;
  }

  /* Back side */
  .services {
    position: absolute; left: 0; right: 0; top: 62px;
    text-align: center; font-size: 19px; line-height: 34px;
  }
  .back__rule {
    position: absolute; left: 91px; width: 296px; top: 209px;
    height: 1px; background: var(--rule-dark);
  }
  .slogan {
    position: absolute; left: 0; right: 0; top: 228px;
    text-align: center; font-size: 19px; text-transform: uppercase;
    letter-spacing: 0.2px;
  }
</style>
</head>
<body>
<main class="stage">
  <section class="card card--front" aria-label="Card front">
    <div class="brand">
      <span class="brand__dot"></span>
      <span class="brand__name">Brisk's Polish Works</span>
    </div>

    <div class="social">
      <span class="social__dot"></span>
      <span class="social__handle">Brisks_Polish_Works</span>
      <span class="social__rule"></span>
    </div>

    <div class="contact">
      <div class="contact__row">
        <svg width="12" height="11" viewBox="0 0 12 11" aria-hidden="true">
          <path d="M1 3 Q6 -1 11 3 L9.5 4.5 L8 3.5 L8 2.5 Q6 2 4 2.5 L4 3.5 L2.5 4.5 Z M3 5 L9 5 L10.5 10 L1.5 10 Z" fill="#000"/>
        </svg>
        <span>208.417.6352</span>
      </div>
      <div class="contact__row">
        <svg width="12" height="11" viewBox="0 0 12 11" aria-hidden="true">
          <rect x="0.5" y="1.5" width="11" height="8" fill="#000"/>
          <path d="M1 2 L6 6 L11 2" stroke="#fff" stroke-width="1" fill="none"/>
        </svg>
        <span>BrisksPolish@mailvexo.com</span>
      </div>
    </div>

    <div class="address">
      <div>3847 E Larkin Ave</div>
      <div>Spokane WA 99214</div>
    </div>
  </section>

  <section class="card card--back" aria-label="Card back">
    <p class="services">We offer services on<br>anything including<br>cars, trucks, motorcycles<br>and RVs.</p>
    <div class="back__rule"></div>
    <p class="slogan">We take pride in your ride</p>
  </section>
</main>
</body>
</html>
```